update of B2B website and conversion to single page

The current website needs to be modernized. I want what is commonly called a single page website. It is not actually a single page. See some examples here:
https://www.plivenor.example/
https://www.quorbel.example/
https://www.trindavex.example/
Most or all graphics will be replaced.
Please see the attached spreadsheet for a rough draft of the home page layout. Convert the existing website at https://www.zolvarin.example/ to a single page website. We will provide the page content. You will provide all of the design, graphics, development, production deployment. etc. The look and feel should be corporate, polished, premium.

```html
<!DOCTYPE html>
<html lang="en">
<head>
<meta charset="utf-8">
<title>Zolvarin Data – Enterprise Data Quality and Master Data Management</title>
<link href="https://fonts.googleapis.com/css2?family=Lato:wght@400;700;900&display=swap" rel="stylesheet">
<style>
:root{
  --navy:#242c6b;
  --navy-deep:#0f1650;
  --band:#2b3577;
  --royal:#1a2a9a;
  --gold:#f5b51c;
  --gold-deep:#ee9f12;
  --gold-light:#f6c430;
  --ink:#333333;
  --muted:#8a8a8a;
  --grey-bg:#e7e7e7;
  --white:#ffffff;
}
*{margin:0;padding:0;box-sizing:border-box}
html,body{width:1200px;height:3273px;overflow:hidden}
body{font-family:'Lato',Arial,sans-serif;color:var(--ink);background:var(--white);position:relative}

/* header */
.site-header{position:absolute;top:0;left:0;width:1200px;height:85px;background:var(--white)}
.brand{position:absolute;left:160px;top:18px;display:flex;align-items:center;gap:12px}
.brand-mark{width:30px;height:30px;border-radius:50%;background:var(--navy)}
.brand-name{font-size:30px;font-weight:900;color:var(--navy);letter-spacing:-.5px}
.main-nav{position:absolute;top:22px;left:480px;display:flex}
.main-nav a{display:block;height:37px;line-height:37px;font-size:17px;color:#222;text-decoration:none;padding:0 21px}
.main-nav a.active{background:var(--gold);color:var(--white);font-weight:700;width:90px;text-align:center;padding:0;margin-right:10px}

/* hero */
.hero{position:absolute;top:85px;left:0;width:1200px;height:609px;
  background:
   radial-gradient(ellipse 380px 300px at 40px 200px,rgba(200,30,50,.8),transparent 70%),
   radial-gradient(ellipse 420px 260px at 1100px 120px,rgba(40,170,200,.6),transparent 70%),
   radial-gradient(ellipse 500px 200px at 700px 420px,rgba(70,60,170,.55),transparent 70%),
   linear-gradient(135deg,#1a0a2a,#0c0f2e 55%,#08182c)}
.hero-title{position:absolute;top:205px;left:0;width:1200px;text-align:center;color:var(--white);font-size:41px;font-weight:700;line-height:48px}
.hero-arrow{position:absolute}
.stats-band{position:absolute;top:694px;left:0;width:1200px;height:94px;background:var(--band);color:var(--white)}
.stat{position:absolute;top:18px;display:flex;align-items:center;gap:14px;font-size:22px;line-height:25px}

/* services */
.section-title{position:absolute;left:0;width:1200px;text-align:center;font-size:35px;font-weight:900;color:var(--navy)}
.service-card{position:absolute;top:929px;height:441px;border-radius:6px;color:var(--white);text-align:center}
.service-card.quality{left:175px;width:402px;background:linear-gradient(180deg,#3a4493,#1b2258)}
.service-card.mdm{left:611px;width:404px;background:linear-gradient(180deg,#f7c830,#ee9a12)}
.card-icon{position:absolute;top:27px;left:50%;margin-left:-80px;width:160px;height:160px;border-radius:50%;display:flex;align-items:center;justify-content:center}
.quality .card-icon{background:rgba(255,255,255,.3)}
.mdm .card-icon{background:rgba(255,255,255,.35)}
.card-icon .inner{width:118px;height:118px;border-radius:50%;background:var(--white);display:flex;align-items:center;justify-content:center}
.card-title{position:absolute;left:0;width:100%;font-size:27px;font-weight:700;line-height:31px}
.card-list{position:absolute;left:0;width:100%;list-style:none;font-size:18px;line-height:37px}
.card-list li::before{content:"\203A";font-weight:900;font-size:26px;margin-right:8px;vertical-align:-2px}

/* connectors */
.connectors{position:absolute;top:1475px;left:0;width:1200px;height:589px;background:var(--grey-bg)}
.connector-box{position:absolute;top:153px;width:268px;height:309px;background:var(--white);border:1px solid #cfcfcf;border-radius:5px;overflow:hidden;text-align:center}
.connector-box h3{height:57px;line-height:57px;color:var(--white);font-size:21px;font-weight:700}
.connector-box.apps h3{background:var(--navy-deep)}
.connector-box.db h3{background:var(--gold-deep)}
.connector-box.files h3{background:#24309a}
.connector-box ul{list-style:none;padding-top:30px;font-size:16px;line-height:29.5px;color:#222}
.connector-box li.soon{color:var(--muted)}

/* support */
.support{position:absolute;top:2064px;left:0;width:1200px;height:521px}
.support-copy{position:absolute;left:0;top:0;width:600px;height:521px;color:var(--white);
  background:radial-gradient(ellipse 420px 320px at 120px 420px,#2a44d8,transparent 70%),linear-gradient(160deg,#101c8a,#0a1470 60%,#0c1a8a)}
.support-photo{position:absolute;left:600px;top:0;width:600px;height:521px;background:linear-gradient(135deg,#d9dde2,#9aa3ad 55%,#4d5660)}
.support h2{position:absolute;left:164px;top:98px;font-size:35px;font-weight:700}
.mode{position:absolute}
.mode h4{font-size:21px;font-weight:900;margin-top:6px}
.mode p{font-size:15px;line-height:26px;opacity:.8}

/* contact */
.contact{position:absolute;top:2585px;left:0;width:1200px;height:557px;background:linear-gradient(90deg,var(--gold-deep),#f3ad16 50%,var(--gold-light) 50%,#f5c12c)}
.contact h2{position:absolute;left:172px;top:88px;font-size:35px;font-weight:700;color:var(--white)}
.contact-item{position:absolute;left:168px;display:flex;align-items:center;gap:17px;color:var(--white);font-size:20px;font-weight:700;line-height:28px}
.contact-icon{width:64px;height:64px;border-radius:50%;background:rgba(255,255,255,.35);display:flex;align-items:center;justify-content:center;flex:none}
.contact-icon .inner{width:50px;height:50px;border-radius:50%;background:var(--white);display:flex;align-items:center;justify-content:center}
.field{position:absolute;left:648px;width:390px;border:2px solid rgba(255,255,255,.85);color:var(--white);font-size:15px;font-weight:700;padding:6px 14px}
.submit{position:absolute;left:648px;top:395px;width:140px;height:42px;background:var(--navy-deep);color:var(--white);font-size:16px;font-weight:700;text-align:center;line-height:42px}

/* footer */
.site-footer{position:absolute;top:3142px;left:0;width:1200px;height:131px;background:var(--white);text-align:center}
.site-footer p{position:absolute;top:24px;width:100%;font-size:15px;color:#333}
.social{position:absolute;top:70px;left:0;width:1200px;display:flex;justify-content:center;gap:30px}
.social span{width:16px;height:16px;border-radius:50%;background:var(--navy)}
</style>
</head>
<body>

<header class="site-header">
  <div class="brand"><span class="brand-mark"></span><span class="brand-name">Zolvarin Data</span></div>
  <nav class="main-nav">
    <a class="active" href="#">Home</a>
    <a href="#">Services</a>
    <a href="#">Rich connectors</a>
    <a href="#">Support</a>
    <a href="#">Contact us</a>
  </nav>
</header>

<section class="hero" role="img" aria-label="Abstract glowing data wave and network particles in red, purple and teal">
  <h1 class="hero-title">Enterprise Data Quality and Master<br>Data Management Made Easy</h1>
  <svg class="hero-arrow" style="left:58px;top:230px" width="26" height="56" viewBox="0 0 26 56"><path d="M24 2 L3 28 L24 54" fill="none" stroke="#fff" stroke-width="3"/></svg>
  <svg class="hero-arrow" style="left:1100px;top:230px" width="26" height="56" viewBox="0 0 26 56"><path d="M2 2 L23 28 L2 54" fill="none" stroke="#fff" stroke-width="3"/></svg>
  <svg class="hero-arrow" style="left:606px;top:390px" width="28" height="40" viewBox="0 0 28 40"><path d="M14 2 V36 M3 25 L14 37 L25 25" fill="none" stroke="#f5b51c" stroke-width="3"/></svg>
</section>

<div class="stats-band">
  <div class="stat" style="left:160px">
    <svg width="48" height="56" viewBox="0 0 48 56" fill="none" stroke="#fff" stroke-width="2.5"><path d="M24 4a14 14 0 0 1 14 14c0 11-14 24-14 24S10 29 10 18A14 14 0 0 1 24 4z"/><circle cx="24" cy="18" r="5"/><ellipse cx="24" cy="48" rx="20" ry="5"/></svg>
    <span>Cleanse addresses<br>in 5 minutes</span>
  </div>
  <div class="stat" style="left:465px">
    <svg width="56" height="58" viewBox="0 0 56 58" fill="none" stroke="#fff" stroke-width="2.5"><rect x="3" y="3" width="36" height="12"/><rect x="3" y="19" width="36" height="12"/><rect x="3" y="35" width="30" height="12"/><circle cx="42" cy="44" r="9"/><path d="M48 50l6 6"/></svg>
    <span>Match and Merge records<br>in 10 minutes</span>
  </div>
  <div class="stat" style="left:818px">
    <svg width="52" height="52" viewBox="0 0 52 52" fill="none" stroke="#fff" stroke-width="2.5"><circle cx="26" cy="26" r="23"/><path d="M26 26 L38 14 M12 26h4 M36 26h4 M26 12v4"/></svg>
    <span>Master records<br>in 60 minutes</span>
  </div>
</div>

<h2 class="section-title" style="top:855px">SERVICES</h2>

<article class="service-card quality">
  <div class="card-icon"><div class="inner">
    <svg width="70" height="70" viewBox="0 0 70 70" fill="none" stroke="#242c6b" stroke-width="3"><circle cx="38" cy="30" r="20"/><path d="M18 30h40 M38 10c-8 10-8 30 0 40 M38 10c8 10 8 30 0 40"/><path d="M24 44 L8 62" stroke-width="6"/></svg>
  </div></div>
  <h3 class="card-title" style="top:210px">Data Quality</h3>
  <ul class="card-list" style="top:266px">
    <li>Global Address Verification</li>
    <li>Data Cleansing/Enrichment</li>
    <li>Match and Merge</li>
  </ul>
</article>

<article class="service-card mdm">
  <div class="card-icon"><div class="inner">
    <svg width="70" height="60" viewBox="0 0 70 60" fill="none" stroke="#ee9a12" stroke-width="3"><rect x="6" y="6" width="58" height="38"/><path d="M26 52h18 M35 44v8"/><circle cx="35" cy="25" r="8"/><path d="M14 16h8 M48 16h8 M14 34h8 M48 34h8"/></svg>
  </div></div>
  <h3 class="card-title" style="top:200px">Master Data<br>Management</h3>
  <ul class="card-list" style="top:277px">
    <li>Integration</li>
    <li>Mastering</li>
    <li>Governance</li>
  </ul>
</article>

<section class="connectors">
  <h2 class="section-title" style="top:74px">RICH CONNECTORS</h2>
  <div class="connector-box apps" style="left:177px">
    <h3>APPLICATIONS</h3>
    <ul><li>Trindavex</li><li>Fieldquill</li><li>Corvanta</li><li>Ostrel Business Suite</li><li class="soon">Meridane Dynamics*</li><li class="soon">Kalvo ERP*</li></ul>
  </div>
  <div class="connector-box db" style="left:465px">
    <h3>DATABASES</h3>
    <ul><li>Ostrel DB</li><li>Tarnbase</li><li>Meridane Query Server</li><li>Veldgres</li><li>Norvik D2</li><li class="soon">Plexora*</li></ul>
  </div>
  <div class="connector-box files" style="left:755px">
    <h3>FILES</h3>
    <ul><li>CSV</li><li>Delimited</li><li>Spreadsheet</li><li class="soon">Coming Soon</li></ul>
  </div>
</section>

<section class="support">
  <div class="support-copy">
    <h2>SUPPORT</h2>
    <div class="mode" style="left:164px;top:174px">
      <svg width="40" height="40" viewBox="0 0 40 40" fill="none" stroke="#fff" stroke-width="2"><rect x="3" y="6" width="34" height="31"/><path d="M3 14h34 M11 2v8 M29 2v8 M10 20h4 M18 20h4 M26 20h4 M10 28h4 M18 28h4 M26 28h4"/></svg>
      <h4>BATCH</h4><p>On your schedule</p>
    </div>
    <div class="mode" style="left:399px;top:174px">
      <svg width="40" height="40" viewBox="0 0 40 40" fill="none" stroke="#fff" stroke-width="2"><rect x="3" y="7" width="34" height="28" rx="2"/><path d="M16 14v14l11-7z"/></svg>
      <h4>STREAMING</h4><p>Always in sync</p>
    </div>
    <div class="mode" style="left:164px;top:312px">
      <svg width="40" height="40" viewBox="0 0 40 40" fill="none" stroke="#fff" stroke-width="2"><circle cx="20" cy="20" r="17"/><path d="M20 9v11l7 5"/></svg>
      <h4>REAL TIME/INTERACTIVE</h4><p>Autocomplete Anything<br>Smart Search</p>
    </div>
  </div>
  <div class="support-photo" role="img" aria-label="Photo of business colleagues reviewing charts on a laptop in a bright office"></div>
</section>

<section class="contact">
  <h2>CONTACT US</h2>
  <div class="contact-item" style="top:166px">
    <div class="contact-icon"><div class="inner"><svg width="26" height="30" viewBox="0 0 26 30" fill="none" stroke="#f0a914" stroke-width="2"><path d="M13 2a9 9 0 0 1 9 9c0 7-9 15-9 15S4 18 4 11a9 9 0 0 1 9-9z"/><circle cx="13" cy="11" r="3"/></svg></div></div>
    <span>1180 Larkmoor Avenue<br>Suite 200 Brenhollow, CA 90217</span>
  </div>
  <div class="contact-item" style="top:245px">
    <div class="contact-icon"><div class="inner"><svg width="26" height="26" viewBox="0 0 26 26" fill="none" stroke="#f0a914" stroke-width="2"><path d="M6 2l4 6-3 3c2 4 4 6 8 8l3-3 6 4-3 4C11 24 2 15 2 5z"/></svg></div></div>
    <span>Phone (555) 014-2291</span>
  </div>
  <div class="contact-item" style="top:322px">
    <div class="contact-icon"><div class="inner"><svg width="28" height="20" viewBox="0 0 28 20" fill="none" stroke="#f0a914" stroke-width="2"><rect x="2" y="2" width="24" height="16"/><path d="M2 2l12 9 12-9"/></svg></div></div>
    <span>support@zolvarin.example</span>
  </div>

  <div class="field" style="top:138px;height:36px">Name</div>
  <div class="field" style="top:186px;height:37px">Email</div>
  <div class="field" style="top:234px;height:37px">Phone</div>
  <div class="field" style="top:282px;height:96px">Message</div>
  <div class="submit">SUBMIT</div>
</section>

<footer class="site-footer">
  <p>© 2018 Company Name &nbsp;All right reserved &nbsp;Term of Use</p>
  <div class="social"><span></span><span></span><span></span></div>
</footer>

</body>
</html>
```